WP website design Pellow - Brantz (Contest)

We need a wordpress design that will incorporate a professional color scheme with company logo in a clean layout. The design needs to consider that this will be developed on a responsive theme. Colors are red and black of the logo and and an accent color. Client wants a 'modern' look.

Industry/Entity Type

It Company

Font styles to use
Serif
Sans Serif

Colors

Designer to choose colors to be used in the design.

Requirements
Must have
• Must Have:
- Navigation: 1) Home; 2) Auctions; 3) Real Estate Listings 4) Assets For Sale 5) Services 6) About Us 7) Contact Us

Site will have slideshow - image is attached. Colors will be those in the logo, red and black with maybe an accent color. A site the client mentions liking is Mubrelbids.com for the use of color and layout.

Widgets: Featured Auctions, 2) Email signup form; 3) Testimonials blog widget; 5) Featured Video; Footer will have affiliation logo and contact info.

Home page content:
We are a family owned and operated business with over 25 years of real estate experience in Clinton and surrounding areas in Western Oklahoma. We know that purchasing a home is one of the most important decisions a person can make, and we strive to make it a successful and enjoyable experience for you!
Enjoy our website and please call if you have any questions or would like to make an appointment to view property!
Also, take a moment to look at our Auction Calendar for upcoming auction dates. Auctions are a great opportunity for great deals and rare finds, not to mention A LOT OF FUN!!

Widgets: 1) Featured Properties; 2) Call to action for Sellers 3) Testimonials blog/widget
Nice to have
• use of dropdown menus

```html
<!DOCTYPE html>
<html lang="en">
<head>
<meta charset="utf-8">
<title>Pellow - Brantz | Auction &amp; Real Estate</title>
<link href="https://fonts.googleapis.com/css2?family=Open+Sans:wght@400;600;700&family=Arimo:wght@400;700&display=swap" rel="stylesheet">
<style>
:root{
  --red:#c01f38;
  --red-bright:#e3243f;
  --red-dark:#a81a30;
  --ink:#231f20;
  --text:#666;
  --text-dark:#444;
  --panel:#efefef;
  --line:#d8d8d8;
  --white:#fff;
  --foot-text:#e6e6e6;
}
*{box-sizing:border-box;margin:0;padding:0}
html,body{width:1200px;height:2586px;overflow:hidden}
body{position:relative;background:var(--white);font-family:"Arimo",Arial,sans-serif;color:var(--text);font-size:12.5px;line-height:24px}
.abs{position:absolute}
h2,h3,h4{font-family:"Open Sans",Arial,sans-serif;font-weight:700;text-transform:uppercase}

/* header */
.brand{left:107px;top:30px;width:200px;height:62px}
.brand-name{font-family:"Open Sans",sans-serif;font-weight:700;font-size:30px;line-height:34px;color:var(--red);letter-spacing:-.5px}
.brand-sub{font-family:"Open Sans",sans-serif;font-weight:600;font-size:13px;color:var(--red);line-height:18px;padding-left:44px}
.search{left:562px;top:36px;width:333px;height:40px;border:1px solid var(--line);display:flex;align-items:center;justify-content:space-between;padding:0 12px;color:#999;font-size:12.5px}
.social{top:36px;width:28px;height:28px;background:#bdbdbd}

/* nav */
.nav{left:0;top:119px;width:1200px;height:69px;background:var(--red);border-bottom:2px solid var(--red-dark)}
.nav ul{list-style:none;display:flex;position:absolute;left:107px;top:0;height:69px}
.nav li{color:var(--white);font-size:13px;text-transform:uppercase;height:69px;display:flex;align-items:center;padding:0 30px}
.nav li.current{background:var(--red-bright);padding:0 33px}
.dropdown{left:362px;top:191px;width:176px}
.dropdown div{background:rgba(192,31,56,.92);color:var(--white);font-size:12.5px;height:44px;line-height:44px;padding-left:13px;margin-bottom:4px;text-transform:uppercase}

/* hero */
.hero{left:0;top:190px;width:1200px;height:462px;background:linear-gradient(180deg,#7d8d4a 0%,#a49360 45%,#c4954f 75%,#b07a3c 100%)}
.hero-arrow{top:392px;width:44px;height:44px}

/* intro / video */
.sec-title{color:var(--red);font-size:21px;letter-spacing:.2px}
.video-title{left:107px;top:690px}
.copy p{margin-bottom:14px}
.intro{left:107px;top:733px;width:664px}
.btn{background:var(--red);color:var(--white);font-size:13px;text-transform:uppercase;text-align:center}
.read-more{left:107px;top:917px;width:134px;height:43px;line-height:43px}
.video{left:802px;top:695px;width:289px;height:264px;border:1px solid var(--line);padding:4px}
.video-frame{width:100%;height:100%;background:linear-gradient(180deg,#6f8fb0 0%,#8a9a7a 45%,#4f5a3a 100%);position:relative}
.video-bar{position:absolute;left:0;bottom:0;width:100%;height:18px;background:#1b1b1b}
.play{position:absolute;left:124px;top:104px}

/* auctions */
.auc-title{left:107px;top:997px}
.auc-intro{left:107px;top:1038px;width:620px}
.card{left:107px;width:622px;height:283px;background:var(--panel)}
.card-photo{position:absolute;left:26px;top:24px;width:195px;height:167px}
.card-title{position:absolute;left:243px;top:20px;color:var(--red);font-size:15px}
.card-text{position:absolute;left:243px;top:50px;width:355px;font-size:12.5px;line-height:24px}
.card-btns{position:absolute;left:26px;top:219px;display:flex;gap:16px}
.card-btns div{width:116px;height:36px;display:flex;align-items:center;justify-content:center;gap:8px;font-size:12.5px}
.b-details{background:var(--red);color:var(--white)}
.b-ghost{border:1px solid var(--line);color:#999;background:var(--panel)}

/* sidebar */
.signup{left:776px;top:1005px;width:315px;height:290px;background:var(--ink);padding:24px 24px}
.signup h4{color:var(--white);font-size:16px;margin-bottom:18px;line-height:22px}
.field{background:var(--white);height:40px;margin-bottom:12px;padding-left:12px;line-height:40px;color:#777;font-size:12px}
.signup .btn{width:122px;height:40px;line-height:40px;font-size:12.5px}
.widget{left:776px;width:315px;border:1px solid var(--line);padding:22px 24px}
.widget h4{color:var(--red);font-size:17px;margin-bottom:12px}
.testi{top:1341px;height:249px}
.testi p{font-size:12px;line-height:24px}
.client{color:var(--red);font-size:12px;margin-top:10px}
.view-all{position:absolute;right:22px;bottom:24px;color:var(--red);font-size:12px;text-decoration:underline}
.blog{top:1633px;height:415px}
.post{display:flex;gap:14px;margin-bottom:20px}
.post-photo{width:96px;height:88px;flex:none}
.post h5{font-family:"Open Sans",sans-serif;font-weight:700;font-size:13px;color:var(--text-dark);text-transform:uppercase;line-height:20px;margin-top:6px}
.post em{font-size:11.5px;color:#888;line-height:28px}

/* partners */
.partners{left:107px;top:2098px;display:flex;gap:17px}
.partner{width:150px;height:105px;border:1px solid var(--line);display:flex;align-items:center;justify-content:center}
.badge{background:#d9d9d9}

/* footer */
.footer{left:0;top:2255px;width:1200px;height:331px;background:var(--ink);color:var(--foot-text)}
.fcol{position:absolute;top:38px;font-size:12.5px;line-height:24px}
.fcol h4{color:var(--white);font-size:15px;margin-bottom:8px;line-height:20px}
.copyright{position:absolute;left:107px;top:268px;font-size:12.5px}
</style>
</head>
<body>

<header>
  <div class="abs brand">
    <div class="brand-name">Pellow - Brantz</div>
    <div class="brand-sub">Auction &amp; Real Estate</div>
  </div>
  <div class="abs search">
    <span>Search here</span>
    <svg width="16" height="16" viewBox="0 0 16 16"><circle cx="6.5" cy="6.5" r="5" fill="none" stroke="#aaa" stroke-width="1.6"/><line x1="10.2" y1="10.2" x2="15" y2="15" stroke="#aaa" stroke-width="1.8"/></svg>
  </div>
  <div class="abs social" style="left:993px"></div>
  <div class="abs social" style="left:1029px"></div>
  <div class="abs social" style="left:1064px"></div>
</header>

<nav class="abs nav">
  <ul>
    <li class="current">Home</li>
    <li>Auctions</li>
    <li>Real Estate Listings</li>
    <li>Assets For Sale</li>
    <li>Services</li>
    <li>About Us</li>
    <li>Contact Us</li>
  </ul>
</nav>

<section class="abs hero" role="img" aria-label="Slideshow photo: auction sign on a wire fence in a dry grass field"></section>
<svg class="abs hero-arrow" style="left:25px" viewBox="0 0 44 44"><circle cx="22" cy="22" r="20" fill="rgba(255,255,255,.25)" stroke="#fff" stroke-width="2"/><path d="M25 13 L16 22 L25 31" fill="none" stroke="#fff" stroke-width="3"/></svg>
<svg class="abs hero-arrow" style="left:1130px" viewBox="0 0 44 44"><circle cx="22" cy="22" r="20" fill="rgba(255,255,255,.25)" stroke="#fff" stroke-width="2"/><path d="M19 13 L28 22 L19 31" fill="none" stroke="#fff" stroke-width="3"/></svg>

<div class="abs dropdown">
  <div>Loreum Ipsum Dolor</div>
  <div>Loreum Ipsum Dolor</div>
</div>

<main>
  <h2 class="abs sec-title video-title">Featured Video</h2>
  <div class="abs copy intro">
    <p>Lorem ipsum dolor sit amet, ponderum definitiones sea ea, et habeo gubergren reformidans sit, an doctus audiam utroque ius. Nostrud fuisset consequuntur qui te, partem patrioque sadipscing ea mei, eos ad dicta possim. Lorem ipsum dolor sit amet, ponderum definitiones sea ea, et habeo gubergren reformidans sit, an doctus.</p>
    <p>Lorem ipsum dolor sit amet, ponderum definitiones sea ea, et habeo gubergren reformidans sit, an doctus audiam utroque ius. Nostrud fuisset consequuntur qui te, partem patrioque sadipscing ea mei, eos ad dicta possim. Lorem ipsum dolor sit amet, ponderum definitiones sea ea, et habeo gubergren reformidans sit, an doctus.</p>
  </div>
  <div class="abs btn read-more">Read More</div>

  <div class="abs video">
    <div class="video-frame" role="img" aria-label="Video still of a two-storey family house with lawn">
      <svg class="play" width="40" height="30" viewBox="0 0 40 30"><rect width="40" height="30" rx="6" fill="#fff" opacity=".9"/><path d="M16 9 L26 15 L16 21Z" fill="#333"/></svg>
      <div class="video-bar"></div>
    </div>
  </div>

  <h2 class="abs sec-title auc-title">Featured Auctions</h2>
  <p class="abs auc-intro">Pri ad novum affert voluptua. At quo dico fastidii rationibus. Graeco suavitate vis cu, nam cu suas hinc incorrupte, Pri ad novum affert voluptua. At quo dico fastidii rationibus.</p>

  <article class="abs card" style="top:1114px">
    <div class="card-photo" role="img" aria-label="Photo of a white two-storey house under blue sky" style="background:linear-gradient(180deg,#6a9ad0 0%,#c9ccd0 50%,#6d8a4a 100%)"></div>
    <h3 class="card-title">Loreum Ipsum Dolor</h3>
    <p class="card-text">Lorem ipsum dolor sit amet, ponderum definitiones sea ea, et habeo gubergren reformidans sit, an doctus audiam utroque ius. Nostrud fuisset consequuntur qui te, partem Lorem ipsum dolor sit amet, ponderum definitiones sea ea, et habeo gubergren reformidans sit, an doctus audiam utroque ius.</p>
    <div class="card-btns">
      <div class="b-details"><svg width="14" height="14" viewBox="0 0 16 16"><circle cx="6.5" cy="6.5" r="4.8" fill="none" stroke="#fff" stroke-width="2"/><line x1="10" y1="10" x2="15" y2="15" stroke="#fff" stroke-width="2.4"/></svg>Details</div>
      <div class="b-ghost"><svg width="14" height="12" viewBox="0 0 14 12"><rect y="2" width="14" height="10" rx="1.5" fill="#aaa"/><rect x="4" width="6" height="3" fill="#aaa"/><circle cx="7" cy="7" r="2.6" fill="#efefef"/></svg>Photos</div>
      <div class="b-ghost"><svg width="14" height="10" viewBox="0 0 14 10"><rect width="9" height="10" rx="1.5" fill="#aaa"/><path d="M9 5 L14 1 V9Z" fill="#aaa"/></svg>Videos</div>
    </div>
  </article>

  <article class="abs card" style="top:1438px">
    <div class="card-photo" role="img" aria-label="Photo of a grey-green two-storey house with garage" style="background:linear-gradient(180deg,#8fb0d6 0%,#7d7d72 55%,#6e6a62 100%)"></div>
    <h3 class="card-title">Loreum Ipsum Dolor</h3>
    <p class="card-text">Lorem ipsum dolor sit amet, ponderum definitiones sea ea, et habeo gubergren reformidans sit, an doctus audiam utroque ius. Nostrud fuisset consequuntur qui te, partem Lorem ipsum dolor sit amet, ponderum definitiones sea ea, et habeo gubergren reformidans sit, an doctus audiam utroque ius.</p>
    <div class="card-btns">
      <div class="b-details"><svg width="14" height="14" viewBox="0 0 16 16"><circle cx="6.5" cy="6.5" r="4.8" fill="none" stroke="#fff" stroke-width="2"/><line x1="10" y1="10" x2="15" y2="15" stroke="#fff" stroke-width="2.4"/></svg>Details</div>
      <div class="b-ghost"><svg width="14" height="12" viewBox="0 0 14 12"><rect y="2" width="14" height="10" rx="1.5" fill="#aaa"/><rect x="4" width="6" height="3" fill="#aaa"/><circle cx="7" cy="7" r="2.6" fill="#efefef"/></svg>Photos</div>
      <div class="b-ghost"><svg width="14" height="10" viewBox="0 0 14 10"><rect width="9" height="10" rx="1.5" fill="#aaa"/><path d="M9 5 L14 1 V9Z" fill="#aaa"/></svg>Videos</div>
    </div>
  </article>

  <article class="abs card" style="top:1762px">
    <div class="card-photo" role="img" aria-label="Photo of a cream villa with red tile roof and palm trees" style="background:linear-gradient(180deg,#3f6fb8 0%,#d8cdb5 50%,#3f7a32 100%)"></div>
    <h3 class="card-title">Loreum Ipsum Dolor</h3>
    <p class="card-text">Lorem ipsum dolor sit amet, ponderum definitiones sea ea, et habeo gubergren reformidans sit, an doctus audiam utroque ius. Nostrud fuisset consequuntur qui te, partem Lorem ipsum dolor sit amet, ponderum definitiones sea ea, et habeo gubergren reformidans sit, an doctus audiam utroque ius.</p>
    <div class="card-btns">
      <div class="b-details"><svg width="14" height="14" viewBox="0 0 16 16"><circle cx="6.5" cy="6.5" r="4.8" fill="none" stroke="#fff" stroke-width="2"/><line x1="10" y1="10" x2="15" y2="15" stroke="#fff" stroke-width="2.4"/></svg>Details</div>
      <div class="b-ghost"><svg width="14" height="12" viewBox="0 0 14 12"><rect y="2" width="14" height="10" rx="1.5" fill="#aaa"/><rect x="4" width="6" height="3" fill="#aaa"/><circle cx="7" cy="7" r="2.6" fill="#efefef"/></svg>Photos</div>
      <div class="b-ghost"><svg width="14" height="10" viewBox="0 0 14 10"><rect width="9" height="10" rx="1.5" fill="#aaa"/><path d="M9 5 L14 1 V9Z" fill="#aaa"/></svg>Videos</div>
    </div>
  </article>

  <aside>
    <div class="abs signup">
      <h4>Email Signup Form</h4>
      <div class="field">Enter your first name</div>
      <div class="field">Enter your last name</div>
      <div class="field">Enter your email</div>
      <div class="btn">Signup Now</div>
    </div>

    <div class="abs widget testi">
      <h4>Testimonials</h4>
      <p>Pri ad novum affert voluptua. At quo dico fastidii rationibus. Graeco suavitate vis cu, nam cu suas hinc incorrupte, dicat virtute atomorum sed te.</p>
      <div class="client">Client Name</div>
      <div class="view-all">View all</div>
    </div>

    <div class="abs widget blog">
      <h4>Latest Blog</h4>
      <div class="post"><div class="post-photo" role="img" aria-label="Blog photo: house exterior" style="background:linear-gradient(180deg,#8aa8cc,#b59a74 60%,#6c7a45)"></div><div><h5>Quo Ubique Audiam</h5><em>March 22, 2014</em></div></div>
      <div class="post"><div class="post-photo" role="img" aria-label="Blog photo: bright bathroom interior" style="background:linear-gradient(180deg,#efe9df,#d9cbb4)"></div><div><h5>Quo Ubique Audiam</h5><em>March 22, 2014</em></div></div>
      <div class="post"><div class="post-photo" role="img" aria-label="Blog photo: living room interior" style="background:linear-gradient(180deg,#b89a7a,#6e5640)"></div><div><h5>Quo Ubique Audiam</h5><em>March 22, 2014</em></div></div>
    </div>
  </aside>

  <div class="abs partners">
    <div class="partner"><div class="badge" style="width:104px;height:58px"></div></div>
    <div class="partner"><div class="badge" style="width:52px;height:64px"></div></div>
    <div class="partner"><div class="badge" style="width:64px;height:64px;border-radius:50%"></div></div>
    <div class="partner"><div class="badge" style="width:60px;height:60px;border-radius:50%"></div></div>
    <div class="partner"><div class="badge" style="width:106px;height:56px"></div></div>
    <div class="partner"><div class="badge" style="width:116px;height:36px"></div></div>
  </div>
</main>

<footer class="abs footer">
  <div class="fcol" style="left:107px;width:240px">
    <h4>About Us</h4>
    Lorem ipsum dolor sit amet, id est rebum ipsum, vix simul nullam regione te. Mea ad inani affert scribentur, vix stet audire at, mea ex nisl putent maluisset. Ei principes definitionem has.
  </div>
  <div class="fcol" style="left:399px">
    <h4>Featured Auctions</h4>
    Lorem ipsum dolor sit<br>Ut porro verterem vel eos id<br>Ex qui tale ludus Omnis<br>Ut porro verterem vel<br>Ex qui tale ludus Omnis
  </div>
  <div class="fcol" style="left:631px">
    <h4>Quick Links</h4>
    Auctions<br>Real Estate Listings<br>Assets For Sale<br>Services<br>Contact Us
  </div>
  <div class="fcol" style="left:808px">
    <h4>Contact Info</h4>
    Address :<br>1280 Alder Lane, Westbrook, D07 42KM<br><span style="display:block;height:6px"></span>Phone :<br>1(555) 014-2297
  </div>
  <div class="copyright">Copyright @ 2014 PellowBrantzAuctions.All Rights Reserved.</div>
</footer>

</body>
</html>
```